HALT THE CLAIMS

I'm virtually ready to launch my site, but I have a number of edits and modifications that need to be implemented. More importantly, I'm always looking to improve my site, particularly now that I am making my proverbial "FIRST IMPRESSION." Thus, I'm willing to see if there is someone who can add creativity and perhaps improve what I already have, particularly on the All Important Front Page.

```html
<!DOCTYPE html>
<html lang="en">
<head>
<meta charset="utf-8">
<title>Halt The Claims — Affordable Legal Service Plan</title>
<link href="https://fonts.googleapis.com/css2?family=Montserrat:wght@400;500;600;700&display=swap" rel="stylesheet">
<style>
:root{
  --navy:#10295a;
  --navy-deep:#0b1f47;
  --red:#b3121c;
  --ink:#1c1c1c;
  --grey:#5a5a5a;
  --light:#f3f5f9;
  --white:#ffffff;
  --black:#0a0a0a;
}
*{box-sizing:border-box;margin:0;padding:0}
html,body{width:1200px;height:4307px;overflow:hidden}
body{font-family:'Montserrat',sans-serif;color:var(--ink);background:var(--white);position:relative}
.abs{position:absolute}
.btn{position:absolute;display:flex;align-items:center;justify-content:center;border-radius:26px;font-weight:700;font-size:16px;color:var(--white)}
.btn-red{background:var(--red)}
.btn-navy{background:var(--navy)}
.btn-ghost{border:3px solid var(--white)}
/* header */
.topbar{left:340px;top:0;width:860px;height:46px;background:var(--navy);clip-path:polygon(22px 0,100% 0,100% 100%,0 100%);color:var(--white);font-size:13px;display:flex;align-items:center;gap:46px;padding-left:52px}
.topbar span{display:flex;align-items:center;gap:10px}
.brand{left:118px;top:50px;display:flex;align-items:center;gap:9px;font-weight:700;font-size:15px;color:var(--navy)}
.brand i{width:26px;height:26px;border-radius:50%;background:var(--red);display:block}
.nav{left:366px;top:80px;display:flex;gap:32px;font-size:13px;font-weight:600;color:var(--ink)}
.hero{left:0;top:130px;width:1200px;height:558px;background:linear-gradient(100deg,#1d140e 0%,#3a2719 45%,#6b4a2c 70%,#2a1c12 100%)}
.hero-title{left:108px;top:236px;width:480px;font-size:35px;font-weight:600;line-height:43px;color:var(--white)}
.hero-sub{left:110px;top:420px;font-size:15px;line-height:25px;color:var(--white)}
/* services */
.h2{position:absolute;left:0;width:1200px;text-align:center;font-size:38px;font-weight:500;color:var(--ink)}
.lead{left:0;width:1200px;text-align:center;top:836px;font-size:15px;line-height:26px;color:var(--grey)}
.card{position:absolute;top:927px;width:317px;height:565px;background:var(--white);border-radius:10px;box-shadow:0 3px 10px rgba(0,0,0,.12)}
.card .photo{position:absolute;left:0;top:0;width:317px;height:317px;border-radius:50%;border:4px solid var(--navy)}
.card .badge{position:absolute;left:122px;top:265px;width:72px;height:72px;border-radius:50%;background:var(--white);display:flex;align-items:center;justify-content:center}
.card .badge b{width:58px;height:58px;border-radius:50%;background:var(--navy);display:flex;align-items:center;justify-content:center}
.card h3{position:absolute;top:360px;left:0;width:100%;text-align:center;font-size:21px;font-weight:500;line-height:30px}
.card p{position:absolute;top:438px;left:22px;width:273px;text-align:center;font-size:13px;line-height:26px;color:var(--grey)}
.arrow{position:absolute;top:1199px;width:38px;height:38px;border-radius:50%;background:var(--navy);display:flex;align-items:center;justify-content:center}
/* cta */
.cta{left:0;top:1589px;width:1200px;height:308px;background:linear-gradient(90deg,var(--navy-deep),#163670 60%,var(--navy-deep))}
/* about */
.frame{left:312px;top:2000px;width:262px;height:100px;border:2px solid var(--navy);border-bottom:none;border-radius:4px 4px 0 0}
.about-photo{left:110px;top:2045px;width:428px;height:345px;background:linear-gradient(120deg,#8a929c,#c9c3b8 50%,#3d4656);box-shadow:0 4px 14px rgba(0,0,0,.2)}
.about-body{left:598px;top:2050px;width:420px;font-size:16.5px;font-weight:500;line-height:28px;color:#333}
.about-small{left:598px;top:2250px;width:420px;font-size:13.5px;line-height:26px;color:var(--grey)}
/* contact */
.contact{left:0;top:2485px;width:1200px;height:728px;background:var(--navy)}
.callback{left:107px;top:2560px;width:483px;height:570px;background:var(--navy-deep);border-radius:6px}
.field{position:absolute;left:134px;width:432px;border:2px solid #c9d1e2;border-radius:6px;color:var(--white);font-size:13px;padding:16px 14px}
.map{left:618px;top:2787px;width:453px;height:331px;background:#eceef2;border-radius:8px}
.contact-line{position:absolute;display:flex;gap:16px;color:var(--white);font-size:14px;font-weight:600;line-height:23px}
/* faq */
.faq{position:absolute;left:160px;width:885px;background:var(--white);border-radius:10px;box-shadow:0 3px 12px rgba(0,0,0,.12);display:flex;align-items:center;justify-content:space-between;padding:0 27px;font-size:15px;font-weight:500;line-height:28px}
/* footer */
.footer{left:0;top:3969px;width:1200px;height:338px;background:var(--black);color:var(--white)}
.fcol{color:var(--white)}
.fcol h4{font-size:23px;font-weight:600;margin-bottom:14px;color:var(--white)}
.fcol a{display:block;font-size:14px;line-height:30px;color:var(--white);text-decoration:none}
</style>
</head>
<body>

<!-- header -->
<div class="abs topbar">
  <span><svg width="26" height="26" viewBox="0 0 26 26"><circle cx="13" cy="13" r="12" fill="none" stroke="#fff" stroke-width="1.5"/><path d="M9 7l2.5 0 1 3-1.5 1.2a7 7 0 0 0 3.8 3.8L16 13.5l3 1v2.5c-5 .5-10.5-5-10-10z" fill="#fff"/></svg>(555) 010-2046 / (555) 010-3187</span>
  <span><svg width="26" height="26" viewBox="0 0 26 26"><circle cx="13" cy="13" r="12" fill="none" stroke="#fff" stroke-width="1.5"/><rect x="7" y="9" width="12" height="8" rx="1" fill="none" stroke="#fff" stroke-width="1.5"/><path d="M7 9l6 5 6-5" fill="none" stroke="#fff" stroke-width="1.5"/></svg>4820 Meridian Ave., Suite 210 Sample City, State</span>
</div>
<div class="abs brand"><i></i>HALT THE CLAIMS</div>
<nav class="abs nav"><span>HOME</span><span>ABOUT</span><span>SERVICES</span><span>FAQ</span><span>CONTACT US</span></nav>
<div class="btn btn-navy" style="left:805px;top:65px;width:283px;height:47px;font-size:17px">Schedule Free Consultation</div>

<!-- hero -->
<div class="abs hero" role="img" aria-label="Photo of a courtroom with a judge at the bench"></div>
<h1 class="abs hero-title">BUSINESS OWNERS: Halt The Claims (HTC) Is An Extremely Affordable Legal Service Plan</h1>
<p class="abs hero-sub">Contact us to find out how you can join us to<br>HALT THE CLAIMS!!</p>
<div class="btn btn-ghost" style="left:110px;top:493px;width:160px;height:46px">Learn More</div>
<div class="btn btn-red" style="left:292px;top:493px;width:284px;height:46px">Schedule Free Consultation</div>

<!-- services -->
<h2 class="h2" style="top:772px">OUR SERVICES</h2>
<p class="abs lead">The price for a membership is a ridiculously low $9.95 PER WEEK. We believe that this<br>fee is very affordable. So what is it? Membership includes the following:</p>

<div class="arrow" style="left:23px"><svg width="16" height="16" viewBox="0 0 16 16"><path d="M10 3L5 8l5 5" fill="none" stroke="#fff" stroke-width="2.5"/></svg></div>
<div class="arrow" style="left:1139px"><svg width="16" height="16" viewBox="0 0 16 16"><path d="M6 3l5 5-5 5" fill="none" stroke="#fff" stroke-width="2.5"/></svg></div>

<div class="card" style="left:107px">
  <div class="photo" role="img" aria-label="Close-up photo of a contract document and pen" style="background:linear-gradient(135deg,#f4f4f4,#c8c8c8)"></div>
  <div class="badge"><b><svg width="26" height="26" viewBox="0 0 26 26"><rect x="5" y="3" width="14" height="20" rx="2" fill="none" stroke="#fff" stroke-width="2"/><path d="M8 9h8M8 13h8M8 17h5" stroke="#fff" stroke-width="2"/></svg></b></div>
  <h3>PROPRIETARY<br>CONTRACT LANGUAGE</h3>
  <p>HTC members are entitled to incorporate exclusive proprietary contract language in their contracts, work orders, and other written</p>
</div>
<div class="card" style="left:438px">
  <div class="photo" role="img" aria-label="Photo of two businessmen shaking hands" style="background:linear-gradient(135deg,#d9dbdd,#6d7177)"></div>
  <div class="badge"><b style="background:#6b6b6b"><svg width="26" height="26" viewBox="0 0 26 26"><circle cx="13" cy="9" r="5" fill="#fff"/><path d="M4 23c0-6 4-8 9-8s9 2 9 8z" fill="#fff"/></svg></b></div>
  <h3>FREE INITIAL<br>CONSULTATION</h3>
  <p>As a prospective Halt The Claims ("HTC") member, we urge you to schedule a first consultation with us – at no charge – where we go over</p>
</div>
<div class="card" style="left:767px">
  <div class="photo" role="img" aria-label="Photo of hands reviewing a letter at a desk" style="background:linear-gradient(135deg,#b9bcc0,#3b3e44)"></div>
  <div class="badge"><b><svg width="26" height="26" viewBox="0 0 26 26"><rect x="5" y="3" width="14" height="20" rx="2" fill="none" stroke="#fff" stroke-width="2"/><path d="M8 9h8M8 13h8M8 17h5" stroke="#fff" stroke-width="2"/></svg></b></div>
  <h3>FREE ATTORNEY<br>LETTERS</h3>
  <p>In addition to free monthly consultations, HTC members can have their local HTC Attorney send out a letter about their business, once</p>
</div>

<!-- cta -->
<div class="abs cta" role="img" aria-label="Navy-tinted photo of people in a meeting"></div>
<h2 class="h2" style="top:1675px;color:var(--white);font-size:40px">CONTACT US FOR A FREE CONSULTATION</h2>
<div class="btn btn-red" style="left:459px;top:1758px;width:281px;height:43px">Schedule Free Consultation</div>

<!-- about -->
<div class="abs frame"></div>
<div class="abs about-photo" role="img" aria-label="Photo of a smiling attorney talking with a client at a desk"></div>
<h2 class="abs" style="left:598px;top:1982px;font-size:40px;font-weight:500">ABOUT US</h2>
<p class="abs about-body">HTC is a group of attorney and legal assistants with many years of experience in litigation, who are devoted to PREVENTING LEGAL CLAIMS and COSTLY LAWSUITS through a variety of FREE and VERY AFFORDABLE services described below. OUR UNIQUE SERVICE PLAN MAKES IT POSSIBLE FOR US TO HALT THE CLAIMS.</p>
<p class="abs about-small">A homebuilding company was sued by a former employee who claimed to have been promised a more favorable sales area, which claim was disputed by the homebuilder. There</p>
<div class="btn btn-navy" style="left:598px;top:2344px;width:214px;height:46px">Read More</div>

<!-- contact -->
<div class="abs contact" role="img" aria-label="Navy-tinted photo of an office"></div>
<div class="abs callback"></div>
<h2 class="abs" style="left:131px;top:2612px;font-size:36px;font-weight:700;color:var(--white);white-space:nowrap">REQUEST A CALLBACK</h2>
<div class="field" style="top:2707px;height:49px">Your Name</div>
<div class="field" style="top:2767px;height:49px">Email Address</div>
<div class="field" style="top:2827px;height:49px">Phone Number</div>
<div class="field" style="top:2887px;height:106px">Message</div>
<div class="btn btn-red" style="left:242px;top:3036px;width:213px;height:42px">Send Message</div>

<h2 class="abs" style="left:618px;top:2566px;font-size:36px;font-weight:700;color:var(--white)">Contact US</h2>
<div class="contact-line" style="left:624px;top:2646px">
  <svg width="24" height="24" viewBox="0 0 24 24"><path d="M12 2a7 7 0 0 0-7 7c0 5 7 13 7 13s7-8 7-13a7 7 0 0 0-7-7z" fill="#fff"/><circle cx="12" cy="9" r="2.6" fill="#10295a"/></svg>
  <span>4820 MERIDIAN AVE.,<br>SUITE 210,<br>SAMPLE CITY, ST 00000</span>
</div>
<div class="contact-line" style="left:874px;top:2648px">
  <svg width="24" height="24" viewBox="0 0 24 24"><path d="M5 3h4l2 5-2.5 1.5a11 11 0 0 0 6 6L16 13l5 2v4c-9 1-17-7-16-16z" fill="#fff"/></svg>
  <span>(555) 010-2046</span>
</div>
<div class="contact-line" style="left:624px;top:2730px">
  <svg width="24" height="24" viewBox="0 0 24 24"><path d="M5 3h4l2 5-2.5 1.5a11 11 0 0 0 6 6L16 13l5 2v4c-9 1-17-7-16-16z" fill="#fff"/></svg>
  <span>(555) 010-3187</span>
</div>
<div class="abs map" role="img" aria-label="Street map showing the office location"></div>

<!-- faq -->
<h2 class="h2" style="top:3302px">FREQUENTLY ASKED QUESTIONS</h2>
<div class="faq" style="top:3382px;height:84px"><span>Why should I be concerned about legal claims?</span><svg width="20" height="12" viewBox="0 0 20 12"><path d="M0 0h20L10 12z" fill="#111"/></svg></div>
<div class="faq" style="top:3486px;height:83px"><span>Provide more details about the value of HTC's contract language.</span><svg width="20" height="12" viewBox="0 0 20 12"><path d="M0 0h20L10 12z" fill="#111"/></svg></div>
<div class="faq" style="top:3588px;height:83px"><span>If I'm a contractor, for example, how can an HTC membership minimize legal claims against my<br>business?</span><svg width="20" height="12" viewBox="0 0 20 12"><path d="M0 0h20L10 12z" fill="#111"/></svg></div>
<div class="faq" style="top:3689px;height:82px"><span>What does an HTC membership cost?</span><svg width="20" height="12" viewBox="0 0 20 12"><path d="M0 0h20L10 12z" fill="#111"/></svg></div>
<div class="faq" style="top:3790px;height:83px"><span>Do you have a Referral Program?</span><svg width="20" height="12" viewBox="0 0 20 12"><path d="M0 0h20L10 12z" fill="#111"/></svg></div>

<!-- footer -->
<div class="abs footer"></div>
<div class="abs" style="left:110px;top:4076px;display:flex;align-items:center;gap:8px;color:var(--white);font-weight:700;font-size:14px;width:190px">
  <i style="width:22px;height:22px;border-radius:50%;background:var(--red);display:block"></i>HALT THE CLAIMS
</div>
<div class="abs" style="left:110px;top:4168px;display:flex;gap:22px">
  <i style="width:30px;height:30px;border-radius:50%;border:2px solid #fff;display:block"></i>
  <i style="width:30px;height:30px;border-radius:50%;border:2px solid #fff;display:block"></i>
  <i style="width:30px;height:30px;border-radius:50%;border:2px solid #fff;display:block"></i>
</div>
<div class="abs fcol" style="left:383px;top:4046px"><h4>Quick links</h4><a>HOME</a><a>ABOUT</a><a>SERVICES</a><a>FAQ</a></div>
<div class="abs fcol" style="left:612px;top:4046px"><h4>Other links</h4><a>CONTACT US</a><a>TERMS OF SERVICE</a><a>PRIVACY POLICY</a></div>
<div class="abs fcol" style="left:859px;top:4046px;width:240px"><h4>Contact Info</h4>
  <a>&#9742; (555) 010-3187</a><a>&#9742; (555) 010-2046</a><a style="line-height:28px">&#9679; 4820 MERIDIAN AVE.,<br>&nbsp;&nbsp;&nbsp;SUITE 210, SAMPLE CITY,<br>&nbsp;&nbsp;&nbsp;ST 00000</a>
</div>
<div class="abs" style="left:107px;top:4261px;width:978px;height:1px;background:#555"></div>
<p class="abs" style="left:0;width:1200px;text-align:center;top:4277px;font-size:13px;color:var(--white)">Copyright © HALT THE CLAIMS | All Rights Reserved</p>

</body>
</html>
```